Boutique custom software development company needs new business card

Our nearly 20 year old custom software development company would like to better include the fact that we are now providing Bitcoin services. These new services are B2B include education (how to acquire and securely hold Bitcoin) and integrating Bitcoin payments into existing ecommerce sites or other existing systems. Please keep the card clean and simple. Attached is our current design and some other files. vextorial.com

Target Market(s)

businesses owners interested in long term relationship

Industry/Entity Type

Custom software development and Bitcoin

Contact Information for Business Card

Dale Parker, dale@vextorial.com, vextorial.com, (888) 555-VXTRL

Font styles to use
Other font styles liked:
• monospace

Requirements
Must have
• double-sided
Nice to have
• clean and simple
Should not have
• physical address

```html
<!DOCTYPE html>
<html lang="en">
<head>
<meta charset="utf-8">
<title>Vextorial business card</title>
<link rel="stylesheet" href="https://fonts.googleapis.com/css2?family=Montserrat:ital,wght@0,400;0,600;0,800;1,800&family=Lato:wght@400;700&display=swap">
<style>
  :root{
    --stage:#1e1f22;
    --paper:#ffffff;
    --brand-blue:#3d6fba;
    --deep-blue:#2a58a6;
    --light-blue:#6e9ad6;
    --brand-orange:#f07a1c;
    --ink:#3a3a3a;
  }
  *{box-sizing:border-box;margin:0;padding:0}
  html,body{width:1200px;height:900px;overflow:hidden;background:var(--stage)}
  .canvas{position:relative;width:1200px;height:900px}
  .card{position:absolute;left:250px;width:700px;height:400px;overflow:hidden;box-shadow:0 10px 30px rgba(0,0,0,.45)}
  .card--front{top:35px;background:var(--paper)}
  .card--back{top:465px}
  .swoosh{position:absolute;inset:0}
  .brand{position:absolute;left:70px;top:110px}
  .brand__name{font-family:"Montserrat",sans-serif;font-weight:800;font-size:54px;color:var(--brand-blue);letter-spacing:-1px;line-height:1}
  .brand__tagline{font-family:"Lato",sans-serif;font-size:15px;color:var(--brand-blue);margin-top:6px}
  .divider{position:absolute;left:395px;top:100px;width:2px;height:120px;background:var(--brand-blue)}
  .contact{position:absolute;left:420px;top:100px;font-family:"Montserrat",sans-serif;color:var(--ink)}
  .contact__name{font-weight:800;font-style:italic;font-size:23px;color:var(--brand-blue);letter-spacing:.5px;text-transform:uppercase;margin-bottom:12px}
  .contact__line{display:flex;align-items:center;gap:8px;font-size:15px;line-height:24px}
  .contact__line svg{width:13px;height:13px;flex:none}
  .pattern{position:absolute;inset:0;background:linear-gradient(160deg,var(--deep-blue) 0%,var(--brand-blue) 55%,var(--light-blue) 100%)}
  .back-mark{position:absolute;right:70px;bottom:50px;display:flex;align-items:center;gap:10px;background:var(--paper);padding:12px 18px}
  .back-mark__square{width:16px;height:16px;background:var(--brand-orange)}
  .back-mark__name{font-family:"Montserrat",sans-serif;font-weight:800;font-size:24px;color:var(--brand-blue)}
</style>
</head>
<body>
<main class="canvas">
  <section class="card card--front" aria-label="Card front">
    <svg class="swoosh" viewBox="0 0 700 400" preserveAspectRatio="none" aria-hidden="true">
      <path d="M0 215 C 60 300, 300 360, 700 372 L700 400 L0 400 Z" fill="var(--brand-blue)"/>
      <path d="M40 270 C 200 330, 420 355, 700 358" fill="none" stroke="var(--brand-orange)" stroke-width="6"/>
      <path d="M40 276 C 200 338, 420 364, 700 366" fill="none" stroke="var(--paper)" stroke-width="4"/>
    </svg>
    <div class="brand">
      <div class="brand__name">Vextorial</div>
      <div class="brand__tagline">developer of custom applications</div>
    </div>
    <div class="divider"></div>
    <div class="contact">
      <div class="contact__name">Dale Parker</div>
      <div class="contact__line">
        <svg viewBox="0 0 16 16"><path d="M4 1l3 3-2 2c1 2 3 4 5 5l2-2 3 3-2 3C7 15 1 9 1 3z" fill="var(--brand-orange)"/></svg>
        (888) 555-VXTRL
      </div>
      <div class="contact__line">
        <svg viewBox="0 0 16 16"><rect x="1" y="3" width="14" height="10" fill="var(--brand-orange)"/><path d="M1 3l7 6 7-6" fill="none" stroke="var(--paper)" stroke-width="1.5"/></svg>
        dale@vextorial.com
      </div>
      <div class="contact__line">
        <svg viewBox="0 0 16 16"><circle cx="8" cy="8" r="7" fill="var(--brand-orange)"/><path d="M1 8h14M8 1c-3 3-3 11 0 14M8 1c3 3 3 11 0 14" fill="none" stroke="var(--paper)" stroke-width="1"/></svg>
        vextorial.com
      </div>
    </div>
  </section>

  <section class="card card--back" aria-label="Card back">
    <div class="pattern" role="img" aria-label="Repeating brand-mark pattern in tones of blue"></div>
    <div class="back-mark">
      <span class="back-mark__square"></span>
      <span class="back-mark__name">Vextorial</span>
    </div>
  </section>
</main>
</body>
</html>
```